Need CATCHY/VIVID Banner design for my new UTV/ATV/Off Road Vehicle turn signal/lighting company

I need a banner ad designed so I can advertise on several different ATV (all terrain vehicle), UTV (Utility Vehicles), Golf Cart and Off-Road Vehicle forums. Ads need to be very catchy and produce a call to action. Action is getting hits to my website. Our main business is selling turn signal kits to make your side by side or your ATV/UTV street legal, as some states now allow you to drive these on public roads if you have the following items: Turn Signals, Horn, Lighted license plate bracket, headlights and brake lights. We sell all of these items for just about any model vehicle out there. Our call to action for this banner would be to get more website visits.

Target Market(s)

Off-road/outdoor enthusiasts,

Industry/Entity Type

Car Accessorie

Font styles to use
Sans Serif

Requirements
Must have
• Ad size need to be either 728x90 or 300x250. Colorful ad with an off-road vehicle integrated to the design (think UTV, side-by-side, etc.
Nice to have
• Nice to haves would be anything that makes this banner ad stand out on very boring web pages.
Should not have
• anything dull

```html
<!DOCTYPE html>
<html lang="en">
<head>
<meta charset="utf-8">
<title>Trailwise Signal Kits – ATV &amp; UTV Banner</title>
<link href="https://fonts.googleapis.com/css2?family=Archivo:wght@600;700;800&display=swap" rel="stylesheet">
<style>
  :root {
    --red: #e4222a;
    --red-deep: #b5121b;
    --red-dark: #8e0c14;
    --yellow: #ffd31c;
    --yellow-deep: #f2a900;
    --white: #ffffff;
    --vehicle-grey: #9a9a98;
    --vehicle-dark: #2a2a2a;
  }
  * { margin: 0; padding: 0; box-sizing: border-box; }
  html, body { width: 1200px; height: 1000px; overflow: hidden; background: var(--white); }
  .banner {
    position: relative;
    width: 1200px;
    height: 1000px;
    overflow: hidden;
    font-family: "Archivo", "Arial", sans-serif;
    color: var(--white);
    background: linear-gradient(160deg, var(--red) 0%, var(--red-deep) 55%, var(--red-dark) 100%);
  }
  .sand-wedge { position: absolute; inset: 0; }
  .brand {
    position: absolute;
    left: 44px;
    top: 62px;
    display: flex;
    align-items: center;
    gap: 26px;
  }
  .brand-dot {
    width: 120px;
    height: 120px;
    border-radius: 50%;
    background: var(--white);
    flex: none;
  }
  .brand-name {
    font-weight: 700;
    text-transform: uppercase;
    line-height: 1.05;
    color: var(--white);
  }
  .brand-name .line-main { display: block; font-size: 56px; letter-spacing: 1px; }
  .brand-name .line-sub { display: block; font-size: 34px; letter-spacing: 1px; }
  .vehicle-photo {
    position: absolute;
    left: 540px;
    top: 180px;
    width: 660px;
    height: 760px;
    border-radius: 60px 0 0 60px;
    background:
      radial-gradient(ellipse at 60% 45%, var(--vehicle-grey) 0%, rgba(154,154,152,0) 55%),
      linear-gradient(180deg, var(--red) 0%, #c73b2c 25%, #6e6e6c 55%, var(--vehicle-dark) 100%);
    opacity: 0.95;
  }
  .headline {
    position: absolute;
    left: 64px;
    top: 330px;
    font-weight: 800;
    font-size: 104px;
    line-height: 1.05;
    text-transform: uppercase;
    letter-spacing: 1px;
  }
  .subhead {
    position: absolute;
    left: 66px;
    top: 560px;
    font-weight: 600;
    font-size: 52px;
    line-height: 1.2;
    text-transform: uppercase;
    color: var(--yellow);
  }
  .features {
    position: absolute;
    left: 64px;
    top: 784px;
    display: flex;
    gap: 20px;
    list-style: none;
  }
  .feature {
    width: 112px;
    height: 112px;
    border-radius: 50%;
    background: var(--red);
    border: 5px solid var(--white);
    display: flex;
    align-items: center;
    justify-content: center;
  }
  .feature:first-child { margin-right: 40px; }
  .feature svg { width: 70px; height: 70px; }
</style>
</head>
<body>
<main class="banner">
  <svg class="sand-wedge" width="1200" height="1000" viewBox="0 0 1200 1000" aria-hidden="true">
    <defs>
      <linearGradient id="sandGrad" x1="0" y1="0" x2="1" y2="1">
        <stop offset="0" stop-color="#ffe04a"/>
        <stop offset="0.6" stop-color="#ffd31c"/>
        <stop offset="1" stop-color="#f2a900"/>
      </linearGradient>
    </defs>
    <polygon points="1200,80 1200,1000 610,1000" fill="url(#sandGrad)"/>
  </svg>

  <div class="brand">
    <span class="brand-dot" aria-hidden="true"></span>
    <p class="brand-name">
      <span class="line-main">Trailwise Signal Kits</span>
      <span class="line-sub">&amp; Lighting Accessories</span>
    </p>
  </div>

  <div class="vehicle-photo" role="img" aria-label="Photo of a red and grey sport side-by-side UTV with roll cage and off-road tyres, front three-quarter view"></div>

  <h1 class="headline">ATV&amp; UTV<br>Vechicle</h1>
  <p class="subhead">Signal Kits<br>and Lighting</p>

  <ul class="features">
    <li class="feature" aria-label="Brake lights">
      <svg viewBox="0 0 70 70" fill="none" stroke="#fff" stroke-width="5" stroke-linecap="round">
        <circle cx="35" cy="35" r="16"/>
        <path d="M14 20 A22 22 0 0 0 14 50"/>
        <path d="M56 20 A22 22 0 0 1 56 50"/>
        <line x1="35" y1="26" x2="35" y2="37"/>
        <circle cx="35" cy="44" r="1.5" fill="#fff"/>
      </svg>
    </li>
    <li class="feature" aria-label="Headlights">
      <svg viewBox="0 0 70 70" fill="#fff" stroke="#fff" stroke-width="5" stroke-linecap="round">
        <path d="M40 18 C58 18 58 52 40 52 Z" stroke-linejoin="round"/>
        <line x1="12" y1="24" x2="30" y2="24"/>
        <line x1="12" y1="35" x2="30" y2="35"/>
        <line x1="12" y1="46" x2="30" y2="46"/>
      </svg>
    </li>
    <li class="feature" aria-label="Horn">
      <svg viewBox="0 0 70 70" fill="#fff">
        <path d="M10 30 h12 l26 -14 v38 l-26 -14 h-12 z"/>
        <rect x="18" y="40" width="8" height="12" rx="2"/>
        <path d="M54 22 q10 13 0 26" fill="none" stroke="#fff" stroke-width="4" stroke-linecap="round"/>
      </svg>
    </li>
    <li class="feature" aria-label="Turn signals">
      <svg viewBox="0 0 70 70" fill="none" stroke="#fff" stroke-width="4" stroke-linejoin="round">
        <path d="M6 35 L20 22 V29 H30 V41 H20 V48 Z"/>
        <path d="M64 35 L50 22 V29 H40 V41 H50 V48 Z"/>
      </svg>
    </li>
  </ul>
</main>
</body>
</html>
```